FinTech company looking to revamp and expand client-facing interface for our financial models

Pellworth Engines currently has a very simple website that allows clients to interact with our financial models. We are looking to completely redesign the current site and add several extra pages to provide extra functionality. We want the design to have a modern, slick feel, that will work on both a desktop or a tablet. It should be straightforward for clients to move between different pages at any time, and clear from the layout how to interact with the more advanced features. We have included screenshots of existing pages in the attached design brief, as well as sketches of the functionality required by the new pages, but can't provide a direct link to the current site.
Target Market(s)
Professional investors that will be paying to access the interface
Industry/Entity Type
Finance
Number of Pages Required
4 page
Colors
Designer to choose colors to be used in the design.
Look and feel
Each slider illustrates characteristics of the customer's brand and the style your logo design should communicate.

```html
<!DOCTYPE html>
<html lang="en">
<head>
<meta charset="utf-8">
<title>KORVA · Backtest</title>
<link href="https://fonts.googleapis.com/css2?family=Open+Sans:wght@400;600;700&family=Roboto+Condensed:wght@400;500&display=swap" rel="stylesheet">
<style>
:root{
  --navy:#0a3468;
  --teal:#0b6e63;
  --bg:#e8e8e8;
  --panel:#cfcfcf;
  --white:#ffffff;
  --ink:#111111;
  --rule:#e4e4e4;
  --stripe:#f0f0f0;
  --header-grey:#6b6b6b;
  --black:#1a1a1a;
}
*{box-sizing:border-box;margin:0;padding:0}
html,body{width:1200px;height:1122px;overflow:hidden;background:var(--white)}
body{font-family:"Open Sans",Arial,sans-serif;color:var(--ink)}
.stage{position:absolute;left:0;top:0;width:1300px;height:1215px;transform:scale(.9231);transform-origin:0 0}
.abs{position:absolute}
.frame{left:15px;top:15px;width:1270px;height:1185px;background:var(--bg)}
/* top nav */
.topnav{left:15px;top:15px;width:1270px;height:60px;background:var(--white);display:flex;font-weight:700;font-size:14px}
.topnav .item{height:60px;display:flex;align-items:center;justify-content:center;gap:8px;border-right:1px solid var(--rule)}
.brand{width:180px;font-size:19px}
.period{width:90px}
.spacer{width:136px}
.topnav .active{background:var(--navy);color:var(--white);border:none}
/* mode band */
.mode-band{left:105px;top:115px;width:1160px;height:85px;background:#efefef;box-shadow:0 4px 10px rgba(0,0,0,.08)}
.tab{top:115px;width:154px;height:40px;display:flex;align-items:center;justify-content:center;font-size:14px;font-weight:700;border-radius:3px 3px 0 0}
.tab-1{left:258px;background:#d4d4d4}
.tab-2{left:418px;background:var(--navy);color:var(--white)}
/* chart */
.chart-card{left:105px;top:200px;width:1160px;height:340px;background:var(--white)}
.options-tab{left:800px;top:310px;width:50px;height:250px;background:#d4d4d4;border-radius:0 4px 4px 0}
.options-label{left:806px;top:478px;transform:rotate(-90deg);transform-origin:0 0;font-size:17px;font-weight:600;letter-spacing:1px}
/* overlay */
.overlay{left:15px;top:155px;width:785px;height:560px;background:var(--panel)}
.card{background:var(--white)}
.models{left:30px;top:170px;width:370px;height:530px}
.search{left:47px;top:180px;width:181px;height:30px;border:1px solid #ccc;border-radius:3px;font-size:15px;padding:4px 13px;box-shadow:inset 0 1px 2px rgba(0,0,0,.1)}
.btn-select{left:238px;top:180px;width:104px;height:30px;background:var(--teal);color:var(--white);border-radius:3px;font-weight:700;font-size:15px;display:flex;align-items:center;justify-content:center}
.model-list{left:30px;top:220px;width:330px}
.model-row{height:49.5px;border-top:1px solid var(--rule);padding-left:21px;display:flex;align-items:center;font-weight:700;font-size:17px}
.model-row.selected{background:var(--teal);color:var(--white)}
.track{border:1px solid #c8c8c8;border-radius:9px;background:var(--white)}
.thumb{background:#9a9a9a;border-radius:9px}
.btn-add{left:118px;top:640px;width:194px;height:40px;background:var(--navy);color:var(--white);border-radius:3px;display:flex;align-items:center;justify-content:center;gap:12px;font-size:13px;font-weight:700}
.params{left:415px;top:170px;width:370px;height:530px}
.params-head{left:415px;top:170px;width:370px;height:50px;background:var(--header-grey);color:var(--white);font-weight:700;font-size:18px;display:flex;align-items:center;justify-content:center}
.param-row{left:415px;width:370px;height:50px;border-bottom:1px solid var(--rule)}
.param-row .lbl{position:absolute;left:18px;top:13px;font-weight:700;font-size:17px}
.param-row .field{position:absolute;left:114px;top:9px;width:241px;height:31px;border:1px solid #ccc;border-radius:3px;font-size:15px;padding:4px 12px;box-shadow:inset 0 1px 2px rgba(0,0,0,.1)}
.btn-run{left:524px;top:636px;width:153px;height:48px;background:var(--navy);color:var(--white);border-radius:3px;font-weight:700;font-size:15px;display:flex;align-items:center;justify-content:center}
/* export */
.export{left:1174px;top:593px;display:flex;align-items:center;gap:8px;color:var(--navy);font-weight:700;font-size:17px}
/* tables */
.tbl{font-family:"Roboto Condensed",Arial,sans-serif;font-size:17px}
.tbl-head{background:var(--black);color:var(--white);font-family:"Open Sans",Arial,sans-serif;font-weight:600;font-size:17px}
.tr{display:flex}
.td{display:flex;align-items:center;justify-content:center;border-right:1px solid var(--rule)}
.stats{left:105px;top:700px;width:400px;height:420px;background:var(--white);box-shadow:0 4px 10px rgba(0,0,0,.08)}
.trades{left:545px;top:630px;width:720px;height:490px;background:var(--white);box-shadow:0 4px 10px rgba(0,0,0,.08)}
.stripe{background:var(--stripe)}
.col{width:180px}
.col-last{width:140px;border-right:none}
</style>
</head>
<body>
<div class="stage">
  <div class="abs frame"></div>

  <nav class="abs topnav">
    <div class="item brand">KORVA</div>
    <div class="item period">250D</div>
    <div class="item period">83D</div>
    <div class="item period">42D</div>
    <div class="item spacer"></div>
    <div class="item" style="width:140px">
      <svg width="24" height="22" viewBox="0 0 24 22"><path d="M2 11 12 2l10 9M5 9v11h5v-6h4v6h5V9" fill="none" stroke="#111" stroke-width="2.4"/></svg>MODELS</div>
    <div class="item" style="width:177px">
      <svg width="26" height="26" viewBox="0 0 26 26" fill="#111"><circle cx="13" cy="13" r="4"/><g fill="none" stroke="#111" stroke-width="1.6" stroke-dasharray="2 2"><circle cx="13" cy="13" r="8"/><circle cx="13" cy="13" r="11.5"/></g></svg>SENSITIVITIES</div>
    <div class="item" style="width:160px">
      <svg width="24" height="24" viewBox="0 0 24 24" fill="none" stroke="#111" stroke-width="2"><circle cx="6" cy="6" r="4"/><circle cx="18" cy="6" r="4"/><circle cx="6" cy="18" r="4"/><circle cx="18" cy="18" r="4"/></svg>PORTFOLIO</div>
    <div class="item active" style="width:152px">
      <svg width="26" height="22" viewBox="0 0 26 22" fill="none" stroke="#fff" stroke-width="2"><rect x="1" y="1" width="24" height="20"/><path d="M5 16l5-6 4 4 6-8"/><path d="M5 18h16"/></svg>BACKTEST</div>
  </nav>

  <div class="abs mode-band"></div>
  <div class="abs tab tab-1">Mode 1</div>
  <div class="abs tab tab-2">Mode 2</div>

  <div class="abs chart-card">
    <svg class="abs" style="left:0;top:0" width="1160" height="340" viewBox="105 200 1160 340">
      <g stroke="#eeeeee" stroke-width="1">
        <line x1="800" y1="263" x2="1110" y2="263"/><line x1="800" y1="300" x2="1110" y2="300"/>
        <line x1="800" y1="338" x2="1110" y2="338"/><line x1="800" y1="375" x2="1110" y2="375"/>
        <line x1="800" y1="412" x2="1110" y2="412"/>
      </g>
      <line x1="850" y1="450" x2="1110" y2="450" stroke="#999"/>
      <g fill="#c8c43a">
        <circle cx="810" cy="267" r="3.5"/><circle cx="830" cy="267" r="3.5"/><circle cx="850" cy="268" r="3.5"/><circle cx="870" cy="267" r="3.5"/><circle cx="890" cy="268" r="3.5"/><circle cx="910" cy="267" r="3.5"/><circle cx="930" cy="268" r="3.5"/><circle cx="950" cy="268" r="3.5"/><circle cx="970" cy="267" r="3.5"/><circle cx="990" cy="268" r="3.5"/><circle cx="1010" cy="268" r="3.5"/><circle cx="1028" cy="267" r="3.5"/>
      </g>
      <line x1="803" y1="263" x2="1060" y2="263" stroke="#3f6fb4" stroke-width="6" stroke-dasharray="8 4" stroke-linecap="round"/>
      <circle cx="1037" cy="446" r="4" fill="#4ea33a"/><circle cx="1045" cy="446" r="4" fill="#4ea33a"/>
      <g font-family="Open Sans,Arial,sans-serif" font-size="12" fill="#666">
        <text x="891" y="476">May 2019</text><text x="1036" y="476">Jul 2019</text>
      </g>
      <text x="1167" y="265" font-family="Georgia,serif" font-size="11" fill="#444">Names</text>
      <g>
        <circle cx="1149" cy="261" r="3.5" fill="#8fb3d9"/><circle cx="1149" cy="280" r="3.5" fill="#f4b47a"/>
        <circle cx="1149" cy="298" r="3.5" fill="#4ea33a"/><circle cx="1149" cy="317" r="3.5" fill="#e08a8a"/>
        <circle cx="1149" cy="336" r="3.5" fill="#b79ed6"/><circle cx="1149" cy="354" r="3.5" fill="#b79a8e"/>
        <circle cx="1149" cy="373" r="3.5" fill="#efb2d8"/><circle cx="1149" cy="392" r="3.5" fill="#bdbdbd"/>
        <circle cx="1149" cy="410" r="3.5" fill="#c8c43a"/><circle cx="1149" cy="429" r="3.5" fill="#8fd6e0"/>
        <circle cx="1149" cy="448" r="3.5" fill="#3f6fb4"/>
      </g>
    </svg>
  </div>

  <div class="abs export">
    <svg width="26" height="22" viewBox="0 0 26 22" fill="none" stroke="var(--navy)" stroke-width="2.2"><path d="M14 3H3v17h17v-8"/><path d="M10 14c0-6 5-9 12-9m-4-4 4 4-4 4"/></svg>Export</div>

  <!-- stats table -->
  <div class="abs stats tbl">
    <div class="tr" style="height:70px"><div class="td col">Stat 1</div><div class="td col">0.5</div></div>
    <div class="tr stripe" style="height:69px"><div class="td col">Stat 2</div><div class="td col">-3</div></div>
    <div class="tr" style="height:70px"><div class="td col">Stat 3</div><div class="td col">30%</div></div>
    <div class="tr stripe" style="height:69px"><div class="td col">Stat 4</div><div class="td col">0.5</div></div>
    <div class="tr" style="height:70px"><div class="td col">Stat 5</div><div class="td col">-3</div></div>
    <div class="tr stripe" style="height:72px"><div class="td col">Stat 6</div><div class="td col">30%</div></div>
  </div>
  <div class="abs" style="left:465px;top:700px;width:40px;height:420px;background:#f2f2f2"></div>
  <div class="abs track" style="left:476px;top:725px;width:18px;height:370px"></div>
  <div class="abs thumb" style="left:476px;top:725px;width:18px;height:75px"></div>

  <!-- trades table -->
  <div class="abs trades tbl">
    <div class="tr tbl-head" style="height:70px">
      <div class="td col" style="border-color:#444">Open</div><div class="td col" style="border-color:#444">Close</div>
      <div class="td col" style="border-color:#444">Size</div><div class="td col" style="border:none">Return</div>
    </div>
    <div class="tr" style="height:70px"><div class="td col">2018-04-05</div><div class="td col">2018-04-07</div><div class="td col">13</div><div class="td col-last">5%</div></div>
    <div class="tr stripe" style="height:69px"><div class="td col">2018-04-05</div><div class="td col">2018-04-07</div><div class="td col">12</div><div class="td col-last">7%</div></div>
    <div class="tr" style="height:70px"><div class="td col">2018-04-05</div><div class="td col">2018-04-07</div><div class="td col">15</div><div class="td col-last">6%</div></div>
    <div class="tr stripe" style="height:69px"><div class="td col">2018-04-05</div><div class="td col">2018-04-07</div><div class="td col">16</div><div class="td col-last">9%</div></div>
    <div class="tr" style="height:70px"><div class="td col">2018-04-05</div><div class="td col">2018-04-07</div><div class="td col">12</div><div class="td col-last">8%</div></div>
    <div class="tr stripe" style="height:72px"><div class="td col">2018-04-05</div><div class="td col">2018-04-07</div><div class="td col">19</div><div class="td col-last">6%</div></div>
  </div>
  <div class="abs" style="left:1225px;top:700px;width:40px;height:420px;background:#f2f2f2"></div>
  <div class="abs track" style="left:1237px;top:725px;width:18px;height:370px"></div>
  <div class="abs thumb" style="left:1237px;top:725px;width:18px;height:75px"></div>

  <div class="abs options-tab"></div>
  <div class="abs options-label">OPTIONS</div>
  <svg class="abs" style="left:836px;top:421px" width="28" height="28" viewBox="0 0 28 28"><circle cx="14" cy="14" r="13" fill="#fff"/><circle cx="14" cy="14" r="11" fill="var(--navy)"/><path d="M19 14H9m4-4-4 4 4 4" fill="none" stroke="#fff" stroke-width="2.2"/></svg>

  <!-- overlay with model picker and parameters -->
  <div class="abs overlay"></div>
  <div class="abs card models"></div>
  <div class="abs search">Model name</div>
  <div class="abs btn-select">Select</div>
  <div class="abs model-list">
    <div class="model-row">Model 1</div>
    <div class="model-row">Model 2</div>
    <div class="model-row selected">Model 3</div>
    <div class="model-row">Model 4</div>
    <div class="model-row">Model 5</div>
    <div class="model-row">Model 6</div>
    <div class="model-row">Model 7</div>
    <div class="model-row" style="border-bottom:1px solid var(--rule)">Model 8</div>
  </div>
  <div class="abs" style="left:360px;top:220px;width:40px;height:400px;background:#f2f2f2"></div>
  <div class="abs track" style="left:370px;top:245px;width:20px;height:350px"></div>
  <div class="abs thumb" style="left:370px;top:245px;width:20px;height:75px"></div>
  <svg class="abs" style="left:152px;top:350px" width="28" height="36" viewBox="0 0 28 36"><path d="M7 2c2 0 3 1 3 3v10l2-1c1-1 3 0 3 1l1 0c1-1 3 0 3 1l1 0c1-1 3 0 3 2v8c0 4-3 8-7 8h-3c-3 0-5-2-7-5L3 21c-1-2 1-4 3-2l1 1V5c0-2 0-3 0-3z" fill="#fff" stroke="#111" stroke-width="1.6"/></svg>
  <div class="abs btn-add">
    <svg width="22" height="22" viewBox="0 0 22 22" fill="none" stroke="#fff" stroke-width="1.6"><circle cx="11" cy="11" r="9.5"/><path d="M11 6v10M6 11h10"/></svg>ADD A MODEL</div>

  <div class="abs card params"></div>
  <div class="abs params-head">Parameters:</div>
  <div class="abs param-row" style="top:220px"><span class="lbl">Entry:</span><span class="field">0.5</span></div>
  <div class="abs param-row" style="top:270px"><span class="lbl">Exit:</span><span class="field">-0.3</span></div>
  <div class="abs param-row" style="top:320px"><span class="lbl">Lookback:</span><span class="field">5</span></div>
  <div class="abs param-row" style="top:370px"><span class="lbl">Entry:</span><span class="field">0.5</span></div>
  <div class="abs param-row" style="top:420px"><span class="lbl">Exit:</span><span class="field">-0.3</span></div>
  <div class="abs param-row" style="top:470px"><span class="lbl">Lookback:</span><span class="field">5</span></div>
  <div class="abs param-row" style="top:520px"><span class="lbl">Entry:</span><span class="field">0.5</span></div>
  <div class="abs param-row" style="top:570px"><span class="lbl">Exit:</span><span class="field">-0.3</span></div>
  <div class="abs btn-run">RUN</div>
</div>
</body>
</html>
```